Rollway Stays

We are 100% online, promoting accommodation details and booking facilities for wheelchair dependant travellers.
Listings will only be accommodation providers which meet our specific criteria.

Target Market(s)

Wheelchair dependant people and their companions

Industry/Entity Type

Accommodation

Contact Information for Business Card

Name, mobile phone number, email address, website address

```html
<!DOCTYPE html>
<html lang="en">
<head>
<meta charset="utf-8">
<title>Rollway Stays – Business Card</title>
<link rel="stylesheet" href="https://fonts.googleapis.com/css2?family=Michroma&family=Oswald:wght@300;500&family=Roboto:wght@300;400&display=swap">
<style>
  :root {
    --sky: #0aaee8;
    --paper: #ffffff;
    --backdrop: #e9ecef;
    --ink-white: #ffffff;
  }
  * { box-sizing: border-box; margin: 0; padding: 0; }
  html, body { width: 1200px; height: 970px; overflow: hidden; }
  body {
    background: var(--backdrop);
    display: flex;
    flex-direction: column;
    align-items: center;
    justify-content: center;
    gap: 40px;
  }
  .card {
    position: relative;
    width: 760px;
    height: 434px;
    background: var(--paper);
    box-shadow: 0 6px 18px rgba(0,0,0,0.18);
    overflow: hidden;
  }
  .wordmark {
    font-family: "Michroma", sans-serif;
    color: var(--sky);
    letter-spacing: 3px;
    text-transform: uppercase;
    white-space: nowrap;
  }

  /* Front */
  .card-front .band {
    position: absolute;
    left: 0; width: 100%;
    height: 110px;
    background: var(--sky);
  }
  .card-front .band-top { top: 0; }
  .card-front .band-bottom { bottom: 0; }
  .card-front .wordmark {
    position: absolute;
    top: 50%;
    left: 50%;
    transform: translate(-50%, -50%);
    font-size: 40px;
  }

  /* Back */
  .card-back .panel { position: absolute; inset: 0; }
  .card-back .wordmark {
    position: absolute;
    left: 210px;
    top: 318px;
    transform: translate(-50%, -50%);
    font-size: 26px;
  }
  .contact {
    position: absolute;
    left: 444px;
    top: 196px;
    color: var(--ink-white);
  }
  .contact-name {
    font-family: "Oswald", sans-serif;
    font-weight: 500;
    font-size: 30px;
    letter-spacing: 1px;
    text-transform: uppercase;
  }
  .contact-role {
    font-family: "Oswald", sans-serif;
    font-weight: 300;
    font-size: 16px;
    letter-spacing: 2px;
    margin-left: 10px;
    text-transform: uppercase;
  }
  .contact-list {
    list-style: none;
    display: grid;
    grid-template-columns: 120px auto;
    column-gap: 14px;
    row-gap: 16px;
    margin-top: 26px;
    font-family: "Roboto", sans-serif;
    font-weight: 300;
    font-size: 12px;
  }
  .contact-list li { display: flex; align-items: center; gap: 8px; white-space: nowrap; }
  .contact-list .wide { grid-column: 1 / span 2; }
  .icon { width: 20px; height: 20px; flex: none; }
</style>
</head>
<body>

  <section class="card card-front" aria-label="Business card front">
    <div class="band band-top"></div>
    <div class="band band-bottom"></div>
    <p class="wordmark">Rollway Stays</p>
  </section>

  <section class="card card-back" aria-label="Business card back">
    <svg class="panel" viewBox="0 0 760 434" aria-hidden="true">
      <polygon fill="#0aaee8" points="0,0 760,0 760,434 420,434 420,240 402,222 420,204 420,190 0,190"/>
    </svg>
    <p class="wordmark">Rollway Stays</p>

    <div class="contact">
      <p><span class="contact-name">Alex Morgan</span><span class="contact-role">General Manager</span></p>
      <ul class="contact-list">
        <li>
          <svg class="icon" viewBox="0 0 20 20" aria-hidden="true"><circle cx="10" cy="10" r="9" fill="none" stroke="#fff" stroke-width="1.4"/><path d="M7 5.5l2 2-1.2 1.4a6 6 0 0 0 3.3 3.3L12.5 11l2 2-1.5 1.6C9 14.3 5.7 11 5.4 7z" fill="#fff"/></svg>
          020 555 0147
        </li>
        <li>
          <svg class="icon" viewBox="0 0 20 20" aria-hidden="true"><circle cx="10" cy="10" r="9" fill="none" stroke="#fff" stroke-width="1.4"/><rect x="5" y="6.5" width="10" height="7" rx="1" fill="none" stroke="#fff" stroke-width="1.2"/><path d="M5.5 7l4.5 3.5L14.5 7" fill="none" stroke="#fff" stroke-width="1.2"/></svg>
          hello@rollwaystays.com
        </li>
        <li>
          <svg class="icon" viewBox="0 0 20 20" aria-hidden="true"><circle cx="10" cy="10" r="9" fill="none" stroke="#fff" stroke-width="1.4"/><path d="M7 5.5l2 2-1.2 1.4a6 6 0 0 0 3.3 3.3L12.5 11l2 2-1.5 1.6C9 14.3 5.7 11 5.4 7z" fill="#fff"/></svg>
          020 555 0148
        </li>
        <li>
          <svg class="icon" viewBox="0 0 20 20" aria-hidden="true"><circle cx="10" cy="10" r="9" fill="none" stroke="#fff" stroke-width="1.4"/><circle cx="10" cy="10" r="5" fill="none" stroke="#fff" stroke-width="1.1"/><path d="M5 10h10M10 5c-2 3-2 7 0 10M10 5c2 3 2 7 0 10" fill="none" stroke="#fff" stroke-width="1"/></svg>
          www.rollwaystays.com
        </li>
        <li class="wide">
          <svg class="icon" viewBox="0 0 20 20" aria-hidden="true"><circle cx="10" cy="10" r="9" fill="none" stroke="#fff" stroke-width="1.4"/><path d="M10 15s-3.5-3.8-3.5-6.3a3.5 3.5 0 0 1 7 0C13.5 11.2 10 15 10 15z" fill="#fff"/><circle cx="10" cy="8.7" r="1.3" fill="#0aaee8"/></svg>
          14 Harbour Lane, Suite 3, Westfield
        </li>
      </ul>
    </div>
  </section>

</body>
</html>
```